Moravel Aesthetic Doctor

I require an elegant, luxurious looking business card for my aesthetic business. I am a doctor and that will set me aside from competitors. I am planning to provide home and spa based treatments to clients with high expectations. I have attached my logo.

```html
<!DOCTYPE html>
<html lang="en">
<head>
<meta charset="utf-8">
<title>Moravel Aesthetic Doctor – Business Card</title>
<link href="https://fonts.googleapis.com/css2?family=Roboto:wght@300;400;500;700&display=swap" rel="stylesheet">
<style>
  :root {
    --backdrop: #3c3f42;
    --card-front: #7ecbec;
    --card-back: #ffffff;
    --band-blue: #52b8e6;
    --band-grey: #a7a8ab;
    --text-light: #ffffff;
    --text-grey: #9d9ea1;
    --wave-pale: #a9def3;
    --wave-mid: #3fa6dd;
    --wave-deep: #1270c2;
  }
  * { margin: 0; padding: 0; box-sizing: border-box; }
  html, body {
    width: 1200px; height: 801px; overflow: hidden;
    background: var(--backdrop);
    font-family: "Roboto", Arial, sans-serif;
  }
  .stage { position: relative; width: 1200px; height: 801px; }
  .card {
    position: absolute; top: 274px;
    width: 443px; height: 263px; overflow: hidden;
  }

  /* Front */
  .card--front { left: 153px; background: var(--card-front); color: var(--text-light); }
  .portrait-art {
    position: absolute; left: 0; top: 0; width: 204px; height: 263px;
  }
  .details {
    position: absolute; right: 29px; top: 36px; text-align: right;
  }
  .details__name { font-size: 17px; font-weight: 700; line-height: 1; white-space: nowrap; }
  .details__letters { font-size: 12.5px; font-weight: 400; margin-left: 4px; }
  .details__diploma { margin-top: 9px; font-size: 13px; font-weight: 300; line-height: 16px; }
  .contact { margin-top: 26px; list-style: none; font-size: 13px; font-weight: 300; line-height: 15.6px; }
  .contact li { display: flex; justify-content: flex-end; align-items: center; gap: 4px; }
  .contact svg { width: 11px; height: 11px; }
  .social {
    position: absolute; right: 29px; top: 191px; display: flex; gap: 3px;
  }
  .social span {
    width: 18px; height: 18px; border: 1px solid var(--text-light); border-radius: 50%;
  }

  /* Back */
  .card--back { left: 625px; background: var(--card-back); }
  .wordmark {
    position: absolute; left: 0; right: 0; top: 52px;
    display: flex; justify-content: center; align-items: center; gap: 14px;
  }
  .wordmark__ring {
    width: 76px; height: 76px; border: 2px solid var(--text-grey); border-radius: 50%;
  }
  .wordmark__name {
    color: var(--text-grey); font-weight: 300; line-height: 1;
    text-transform: uppercase;
  }
  .wordmark__name span { display: block; }
  .wordmark__main { font-size: 40px; letter-spacing: 4px; }
  .wordmark__sub { font-size: 18px; letter-spacing: 1.6px; margin-top: 6px; }
  .tagline {
    position: absolute; left: 0; right: 0; top: 151px; height: 28px;
    background: var(--band-blue); color: var(--text-light);
    font-size: 13px; text-align: center; line-height: 28px; letter-spacing: 0.2px;
  }
  .services {
    position: absolute; left: 0; right: 0; top: 183px; height: 45px;
    background: var(--band-grey); color: var(--text-light);
    font-size: 13.2px; font-weight: 300; text-align: center;
    padding-top: 6px; line-height: 16px;
  }
  .services .dot { margin: 0 6px; font-size: 9px; vertical-align: 1px; }
</style>
</head>
<body>
<main class="stage">

  <section class="card card--front">
    <svg class="portrait-art" role="img" aria-label="Stylised profile illustration made of flowing blue wave bands" viewBox="0 0 204 263">
      <defs>
        <linearGradient id="waveTone" x1="0" y1="0" x2="0" y2="1">
          <stop offset="0" stop-color="var(--wave-pale)"/>
          <stop offset="0.45" stop-color="var(--wave-mid)"/>
          <stop offset="0.7" stop-color="var(--wave-deep)"/>
          <stop offset="1" stop-color="var(--wave-pale)"/>
        </linearGradient>
      </defs>
      <path d="M0 0 H150 C182 50 192 160 176 263 H0 Z" fill="url(#waveTone)"/>
    </svg>

    <div class="details">
      <p class="details__name">Dr Elsa Varenne<span class="details__letters">MRCPCH MD</span></p>
      <p class="details__diploma">Australasian Diploma of<br>Aesthetic Medicine</p>
      <ul class="contact">
        <li>0800 347 519
          <svg viewBox="0 0 12 12" aria-hidden="true"><path d="M2.5 1 L4.5 3.2 L3.4 4.6 C4.2 6.2 5.8 7.8 7.4 8.6 L8.8 7.5 L11 9.5 L9.8 11 C5.5 10.6 1.4 6.5 1 2.2 Z" fill="none" stroke="currentColor" stroke-width="1.1"/></svg>
        </li>
        <li>elsa@moravel.co.nz
          <svg viewBox="0 0 12 12" aria-hidden="true"><rect x="0.5" y="2.5" width="11" height="7.5" fill="currentColor"/><path d="M0.5 2.5 L6 7 L11.5 2.5" fill="none" stroke="var(--card-front)" stroke-width="1"/></svg>
        </li>
        <li>www.moravel.co.nz
          <svg viewBox="0 0 12 12" aria-hidden="true"><g fill="none" stroke="currentColor" stroke-width="0.9"><circle cx="6" cy="6" r="5.2"/><ellipse cx="6" cy="6" rx="2.3" ry="5.2"/><path d="M0.8 6 H11.2 M1.6 3.4 H10.4 M1.6 8.6 H10.4"/></g></svg>
        </li>
      </ul>
    </div>
    <div class="social" aria-hidden="true"><span></span><span></span></div>
  </section>

  <section class="card card--back">
    <div class="wordmark">
      <span class="wordmark__ring" aria-hidden="true"></span>
      <p class="wordmark__name">
        <span class="wordmark__main">Moravel</span>
        <span class="wordmark__sub">Aesthetic Doctor</span>
      </p>
    </div>
    <p class="tagline">HOME AND SPA BASED TREATMENTS</p>
    <p class="services">
      Dermal injectables<span class="dot">●</span>Plasma facials<span class="dot">●</span>Microneedling<br>
      Skin boosters<span class="dot">●</span>Excessive sweating
    </p>
  </section>

</main>
</body>
</html>
```